Redesign of business card for Cedar Ridge Mechanical

We are looking for a new design for our business cards for Cedar Ridge Mechanical. We are a plumbing & HVAC construction company, operating on the West Coast of Canada and USA. Logo attached.
Industry/Entity Type
Construction - Plumbing & HVAC
Contact Information for Business Card
Name, address, phone numbers, email, website address
Look and feel
Each slider illustrates characteristics of the customer's brand and the style your logo design should communicate.

```html
<!DOCTYPE html>
<html lang="en">
<head>
<meta charset="utf-8">
<title>Cedar Ridge Mechanical – Business Card</title>
<link href="https://fonts.googleapis.com/css2?family=Montserrat:wght@400;700;800&display=swap" rel="stylesheet">
<style>
  :root {
    --backdrop: #2a2a2a;
    --ink: #0b0b0b;
    --paper: #ffffff;
    --text: #2b2b2b;
    --stripe: #8a8a8a;
    --rule: #555555;
  }
  * { box-sizing: border-box; margin: 0; padding: 0; }
  html, body {
    width: 1200px; height: 880px; overflow: hidden;
    background: var(--backdrop);
    font-family: "Montserrat", Arial, sans-serif;
  }
  .stage {
    position: relative; width: 1200px; height: 880px;
  }
  .card {
    position: absolute; width: 620px; height: 354px;
    border-radius: 26px; overflow: hidden;
    box-shadow: 0 14px 30px rgba(0,0,0,.45);
  }
  .card--front { left: 290px; top: 56px; background: var(--ink); }
  .card--back  { left: 290px; top: 470px; background: var(--paper); }

  .brand {
    font-family: "Montserrat", Arial, sans-serif;
    font-weight: 800; text-transform: uppercase;
    line-height: 1.05; letter-spacing: .5px;
    display: flex; align-items: center; gap: 18px;
  }
  .brand__mark { flex: none; }
  .brand--front {
    position: absolute; left: 0; right: 0; top: 0; bottom: 0;
    justify-content: center; color: var(--paper); font-size: 38px;
  }
  .brand--front .brand__mark { width: 70px; height: 70px; border: 9px solid var(--paper); }
  .brand--back {
    position: absolute; left: 34px; top: 100px; width: 290px;
    color: var(--ink); font-size: 25px; gap: 14px;
  }
  .brand--back .brand__mark { width: 50px; height: 50px; border: 7px solid var(--ink); }

  .divider {
    position: absolute; left: 336px; top: 60px; width: 1px; height: 178px;
    background: var(--rule);
  }
  .details {
    position: absolute; left: 360px; top: 40px; color: var(--text);
  }
  .details__name { font-weight: 800; font-size: 22px; color: var(--ink); letter-spacing: .5px; }
  .details__role { font-size: 14px; margin-top: 2px; }
  .details__address { font-size: 14px; margin-top: 12px; line-height: 1.35; }
  .contact { list-style: none; margin-top: 12px; font-size: 14px; }
  .contact li { display: flex; align-items: center; gap: 8px; line-height: 1.55; }
  .contact svg { width: 13px; height: 13px; fill: var(--ink); flex: none; }

  .wave { position: absolute; left: 0; bottom: 0; width: 620px; height: 354px; }
</style>
</head>
<body>
<main class="stage">
  <section class="card card--front" aria-label="Card front">
    <div class="brand brand--front">
      <span class="brand__mark"></span>
      <span>Cedar Ridge<br>Mechanical</span>
    </div>
  </section>

  <section class="card card--back" aria-label="Card back">
    <svg class="wave" viewBox="0 0 620 354" preserveAspectRatio="none" aria-hidden="true">
      <path d="M0 330 C160 322 300 300 410 252 C500 212 560 180 620 170 L620 190 C560 200 500 232 410 272 C300 318 160 338 0 344 Z" fill="var(--stripe)"/>
      <path d="M0 344 C160 338 300 318 410 272 C500 232 560 200 620 190 L620 354 L0 354 Z" fill="var(--ink)"/>
    </svg>

    <div class="brand brand--back">
      <span class="brand__mark"></span>
      <span>Cedar Ridge<br>Mechanical</span>
    </div>

    <div class="divider"></div>

    <div class="details">
      <p class="details__name">DANIEL HAYES</p>
      <p class="details__role">Managing Director</p>
      <p class="details__address">Your address, City<br>State, Zip 1234</p>
      <ul class="contact">
        <li>
          <svg viewBox="0 0 24 24"><path d="M6.6 10.8a15 15 0 0 0 6.6 6.6l2.2-2.2a1 1 0 0 1 1-.25 11.4 11.4 0 0 0 3.6.57 1 1 0 0 1 1 1V20a1 1 0 0 1-1 1A17 17 0 0 1 3 4a1 1 0 0 1 1-1h3.5a1 1 0 0 1 1 1c0 1.25.2 2.45.57 3.6a1 1 0 0 1-.25 1z"/></svg>
          123 456 789
        </li>
        <li>
          <svg viewBox="0 0 24 24"><path d="M2 5h20v14H2z M4 7v.5l8 5 8-5V7l-8 5z" fill-rule="evenodd"/></svg>
          info@yourwebsite.com
        </li>
        <li>
          <svg viewBox="0 0 24 24"><path d="M12 2a10 10 0 1 0 0 20 10 10 0 0 0 0-20zm0 2c1.3 1.6 2.1 3.6 2.3 7H9.7c.2-3.4 1-5.4 2.3-7zM4.1 13h3.6c.1 2.4.6 4.4 1.4 6A8 8 0 0 1 4.1 13zm0-2A8 8 0 0 1 9.1 5c-.8 1.6-1.3 3.6-1.4 6zm5.6 2h4.6c-.2 3.4-1 5.4-2.3 7-1.3-1.6-2.1-3.6-2.3-7zm6.6 0h3.6a8 8 0 0 1-5 6c.8-1.6 1.3-3.6 1.4-6zm0-2c-.1-2.4-.6-4.4-1.4-6a8 8 0 0 1 5 6z"/></svg>
          www.yourwebsite.com
        </li>
      </ul>
    </div>
  </section>
</main>
</body>
</html>
```